New Business Card Design Project

Use the flyer uploaded and website www.brightoakbuilders.com for inspiration.
List Our Services on Backside of business cards
Marcus Delling
Harborline Builders Inc.
Licensed General Contractors
858-471-6093

Contact Information for Business Card

Use the flyer uploaded and website www.brightoakbuilders.com for inspiration. List Our Services on Backside of business cards Marcus Delling Harborline Builders Inc. Licensed General Contractors 858-471-6093

```html
<!DOCTYPE html>
<html lang="en">
<head>
<meta charset="utf-8">
<title>Harborline Builders – Business Cards</title>
<link href="https://fonts.googleapis.com/css2?family=Montserrat:wght@400;500;700&display=swap" rel="stylesheet">
<style>
  :root{
    --stage:#151515;
    --card:#262626;
    --ink:#f2f2f2;
    --ink-soft:#cfcfcf;
    --rule:#9a9a9a;
    --palm-light:#8a8a8a;
    --palm-dark:#262626;
  }
  *{box-sizing:border-box;margin:0;padding:0}
  html,body{width:1200px;height:875px;overflow:hidden;background:var(--stage)}
  body{font-family:"Montserrat",sans-serif;color:var(--ink);position:relative}
  .card{
    position:absolute;top:282px;width:540px;height:310px;
    background:var(--card);border-radius:18px;overflow:hidden;
  }
  .card--back{left:40px}
  .card--front{left:620px}

  .brand{
    position:absolute;font-family:"Montserrat",sans-serif;font-weight:400;
    text-transform:uppercase;letter-spacing:3px;color:var(--ink);white-space:nowrap;
  }
  .card--back .brand{top:30px;right:26px;font-size:17px}
  .card--front .brand{top:120px;right:34px;font-size:19px}

  .backdrop{
    position:absolute;left:0;top:0;width:230px;height:310px;
    background:radial-gradient(ellipse at 45% 30%,var(--palm-light) 0%,#4a4a4a 35%,var(--palm-dark) 75%);
    opacity:.75;
  }

  .services{position:absolute;left:262px;top:78px}
  .services__title{
    font-weight:700;font-size:15px;padding-bottom:5px;
    border-bottom:1px solid var(--rule);display:inline-block;padding-right:28px;
  }
  .services__list{list-style:none;margin-top:8px}
  .services__list li{font-size:11.5px;line-height:18.5px;color:var(--ink);padding-left:14px;position:relative}
  .services__list li::before{
    content:"";position:absolute;left:2px;top:7px;width:4px;height:4px;border-radius:50%;background:var(--ink);
  }

  .person{position:absolute;left:32px;top:176px}
  .person__name{font-weight:700;font-size:20px;line-height:22px}
  .person__role{font-size:11.5px;color:var(--ink-soft);margin-top:1px}

  .contact{position:absolute;left:32px;top:236px;list-style:none}
  .contact li{display:flex;align-items:center;gap:9px;font-size:11.5px;line-height:17px;color:var(--ink)}
  .contact svg{width:11px;height:11px;fill:var(--ink);flex:none}
  .contact .license{padding-left:20px}
</style>
</head>
<body>

<section class="card card--back" aria-label="Card back">
  <div class="backdrop" role="img" aria-label="Faint palm tree decoration"></div>
  <div class="brand">Harborline Builders</div>
  <div class="services">
    <h2 class="services__title">Our Services</h2>
    <ul class="services__list">
      <li>Remodel: Kitchen &amp; Bath</li>
      <li>Painting: Interior &amp; Exterior</li>
      <li>Flooring: Carpet, Vinyl, Wood</li>
      <li>Window: Door Replacement</li>
      <li>Plumbing: Repair &amp; Upgrades</li>
      <li>Energy Efficient Upgrades</li>
      <li>Deck &amp; Patio construction</li>
      <li>Water &amp; Mold Damage</li>
      <li>Garage Renovation</li>
    </ul>
  </div>
</section>

<section class="card card--front" aria-label="Card front">
  <div class="brand">Harborline Builders</div>
  <div class="person">
    <h1 class="person__name">Marcus Delling</h1>
    <p class="person__role">Managing Director</p>
  </div>
  <ul class="contact">
    <li>
      <svg viewBox="0 0 24 24" aria-hidden="true"><path d="M6.6 10.8a15.1 15.1 0 0 0 6.6 6.6l2.2-2.2a1 1 0 0 1 1-.25 11.4 11.4 0 0 0 3.6.57 1 1 0 0 1 1 1V20a1 1 0 0 1-1 1A17 17 0 0 1 3 4a1 1 0 0 1 1-1h3.5a1 1 0 0 1 1 1c0 1.25.2 2.45.57 3.57a1 1 0 0 1-.25 1z"/></svg>
      858-471-6093
    </li>
    <li>
      <svg viewBox="0 0 24 24" aria-hidden="true"><path d="M2 5h20v14H2z M2 5l10 8 10-8" fill="none" stroke="#f2f2f2" stroke-width="2.4"/></svg>
      info@brightoakbuilders.com
    </li>
    <li>
      <svg viewBox="0 0 24 24" aria-hidden="true"><circle cx="12" cy="12" r="9.5" fill="none" stroke="#f2f2f2" stroke-width="2.4"/><path d="M2.5 12h19M12 2.5c3 3 3 16 0 19M12 2.5c-3 3-3 16 0 19" fill="none" stroke="#f2f2f2" stroke-width="1.8"/></svg>
      www.brightoakbuilders.com
    </li>
    <li class="license">CSLB Licensed No. #2046518</li>
  </ul>
</section>

</body>
</html>
```